Design a Cover for a Book on Innovation

I need a design for my book: The Quiet Harvest of Invention
It is about the following:

Innovation is not just for those endowed with special talent or skills in technology. This book describes the thought framework that consists of seven principal differences between the current period and the past. Innovation is happening along these shifts. Understanding the differences can allow for consistent innovation and the identification of real opportunities.
Updates

To All: All of you show great talent as designers. I've added a bit more to the description. Feel free to ask questions. Best, DT

Font styles to use
Sans Serif

Colors

Designer to choose colors to be used in the design.

Requirements
Must have
• It should feel modern and innovative. It should incorporate the meaning of Quiet Harvest.
Nice to have
• It should have the title, and a holder spot for the subtitle and author's name Dara Tovens
Should not have
• It should not be overly busy. Sleek modern design that still gets the point across. Alternatively an image that is a full cover graphic.

```html
<!DOCTYPE html>
<html lang="en">
<head>
<meta charset="utf-8">
<title>The Quiet Harvest of Invention — Book Cover</title>
<link href="https://fonts.googleapis.com/css2?family=Poppins:ital,wght@0,300;0,700;1,300&display=swap" rel="stylesheet">
<style>
  :root {
    --paper: #f2f1ef;
    --paper-edge: #e7e6e3;
    --ink: #1d1d1d;
    --accent-red: #9b1115;
    --leaf-green: #6e9a2a;
    --leaf-deep: #557d1c;
    --glass: #d6dedd;
    --glass-light: #e4e9e8;
  }
  html, body {
    margin: 0;
    padding: 0;
    overflow: hidden;
  }
  body {
    width: 927px;
    height: 1200px;
  }
  .cover {
    position: relative;
    width: 927px;
    height: 1200px;
    overflow: hidden;
    background: radial-gradient(ellipse at 50% 40%, var(--paper) 55%, var(--paper-edge) 100%);
    font-family: "Poppins", sans-serif;
    color: var(--ink);
  }
  .artwork {
    position: absolute;
    border-radius: 10px;
  }
  .artwork--pendant-cluster {
    left: 168px;
    top: 0;
    width: 592px;
    height: 358px;
    background: linear-gradient(180deg,
      rgba(110,154,42,0.55) 0%,
      rgba(110,154,42,0.42) 35%,
      var(--glass) 75%,
      var(--glass-light) 100%);
  }
  .artwork--sprouting-bulb {
    left: 516px;
    top: 0;
    width: 162px;
    height: 846px;
    border-radius: 0 0 80px 80px;
    background: linear-gradient(180deg,
      rgba(85,125,28,0.55) 0%,
      rgba(110,154,42,0.5) 45%,
      var(--leaf-deep) 62%,
      var(--leaf-green) 72%,
      var(--glass) 84%,
      var(--glass-light) 100%);
  }
  .title {
    position: absolute;
    right: 423px;
    top: 562px;
    margin: 0;
    text-align: right;
    font-weight: 300;
    font-size: 51px;
    line-height: 47px;
    letter-spacing: -0.5px;
  }
  .title span { display: block; }
  .title .title__accent { color: var(--accent-red); }
  .subtitle {
    position: absolute;
    left: 0;
    right: 0;
    top: 902px;
    margin: 0;
    text-align: center;
    font-style: italic;
    font-weight: 300;
    font-size: 21px;
    letter-spacing: 0.5px;
    text-transform: uppercase;
  }
  .author {
    position: absolute;
    left: 0;
    right: 0;
    top: 1073px;
    margin: 0;
    text-align: center;
    font-weight: 700;
    font-size: 16px;
    letter-spacing: 0.5px;
    text-transform: uppercase;
  }
</style>
</head>
<body>
  <main class="cover">
    <div class="artwork artwork--pendant-cluster" role="img" aria-label="Cluster of glass light bulbs with green caps hanging on green stems"></div>
    <div class="artwork artwork--sprouting-bulb" role="img" aria-label="A single hanging light bulb whose long green stem sprouts a leaf"></div>

    <h1 class="title">
      <span>The</span>
      <span>Quiet</span>
      <span class="title__accent">Harvest</span>
      <span class="title__accent">of</span>
      <span class="title__accent">Invention.</span>
    </h1>

    <p class="subtitle">A Framework to Simplify the Modern Age</p>

    <p class="author">Dara Tovens</p>
  </main>
</body>
</html>
```